Logo and label design for our product coffee scrub

We need a logo design and a packaging label design for our new brand called "Benny Velvetrix". Best design wins 500$

It's a cosmetic brand with initial product "coffee scrub", which is a body peeling made of coffee, himalayan salt and additives. Brand will target young to middle aged women, who we will address with a very sexy and slightly provocative appeal (pictures of women wearing nothing but our coffee scrub - sample attached). Purpose of the coffee scrub is to target cellulite, stretch marks, psoriasis, varicose veins, eczema and acne.

Packaging that we will use will be a brown stand up pouch (attached) with a dimensions width 13cm, height 22cm and with a front and back sticker (dimensions width 7cm, height 14cm, round corners) or sticker that overlaps from front to back.

Looking forward on receiving your ideas!

Target Market(s)

Brand will targeting young to middle aged european women, who we will address with a very sexy and slightly provocative appeal (pictures of women wearing nothing but our coffee scrub - sample attached)

Industry/Entity Type

Product

Requirements
Must have
• Just an idea for the logo writing to use a handwriting font "Benny Velvetrix".

For the front side of packaging label you could use a picture of a women's body wearing a coffee scrub. Label should be very sexy but not vulgar.
Nice to have
• The back side of the label should have a cheesy pick up line and declaration text (just a sample):

hi babe! so you wanna get dirty! just show me the way to your bath. but first let me give you a proper introduction of myself. my name is benny and i'm a coffee scrub wearing nothing but 250g of finest arabic coffee and sweet orange flavour & lots of other good stuff.

by the way I will help you with cellulite, stretch marks, psoriasis, varicose veins, eczema and acne. i’ll smooth your lumps and bumps with brown sugar & sea salt, moisturise and tone your skin with cold pressed sweet almond oil, and use vitamins & minerals to work wonders from the outside in. then i’ll make us both smell good with a little orange essence.

ingredients:
Coffea Robusta Seed Powder (Coffee), Prunus Amygdalus Dulcis (Sweet Almond) Oil, Water (Aqua), Sodium Chloride (Salt), Sucrose (Brown Sugar). All ingredients organic.

net weight: 200 g

best before date:

barcode

```html
<!DOCTYPE html>
<html lang="en">
<head>
<meta charset="utf-8">
<title>Benny Velvetrix – Coffee Scrub Label</title>
<link rel="stylesheet" href="https://fonts.googleapis.com/css2?family=Oswald:wght@400&family=Dancing+Script:wght@400&family=Lora:ital,wght@0,400;0,700;1,400&family=Open+Sans:wght@400&display=swap">
<style>
  :root {
    --page-bg: #ffffff;
    --label-dark: #1b1113;
    --brand-pink: #e5147f;
    --text-light: #f3ece6;
    --caption-ink: #111111;
    --bean-dark: #2a160c;
    --bean-mid: #5a3219;
    --skin-warm: #a5684a;
    --photo-shadow: #1a0f0d;
  }
  * { box-sizing: border-box; margin: 0; padding: 0; }
  html, body {
    width: 1200px; height: 900px; overflow: hidden;
    background: var(--page-bg);
  }
  .sheet { position: relative; width: 1200px; height: 900px; }

  .label {
    position: absolute; top: 156px; height: 568px;
    border-radius: 22px; overflow: hidden;
    background: var(--label-dark);
  }
  .label--front { left: 20px; width: 560px; }
  .label--back { left: 600px; width: 584px; }

  .caption {
    position: absolute; top: 760px;
    font-family: "Open Sans", sans-serif; font-size: 44px;
    color: var(--caption-ink); text-align: center;
  }
  .caption--front { left: 20px; width: 560px; }
  .caption--back { left: 600px; width: 584px; }

  /* front */
  .model-photo {
    position: absolute; inset: 0 0 58px 0;
    background:
      radial-gradient(ellipse 45% 60% at 28% 55%, var(--skin-warm) 0%, #6e3f2c 45%, transparent 75%),
      linear-gradient(90deg, var(--photo-shadow) 0%, #2b1a17 40%, var(--label-dark) 100%);
  }
  .brand-name {
    position: absolute; left: 280px; top: 120px; width: 250px;
    font-family: "Oswald", sans-serif; font-weight: 400; font-size: 32px;
    letter-spacing: 2px; line-height: 1.2;
    color: var(--text-light); text-align: center;
  }
  .product-name {
    position: absolute; left: 280px; top: 292px; width: 250px;
    border-top: 2px solid var(--brand-pink); border-bottom: 2px solid var(--brand-pink);
    font-family: "Oswald", sans-serif; font-size: 34px; letter-spacing: 1px;
    color: var(--brand-pink); text-align: center; line-height: 46px;
  }
  .product-description {
    position: absolute; left: 270px; top: 356px; width: 270px;
    font-family: "Dancing Script", cursive; font-size: 27px; line-height: 1.25;
    color: var(--text-light); text-align: center;
  }
  .pink-band {
    position: absolute; left: 0; right: 0; height: 14px;
    background: var(--brand-pink);
  }
  .label--front .pink-band { bottom: 58px; }
  .bean-strip {
    position: absolute; left: 0; right: 0; bottom: 0; height: 58px;
    background: linear-gradient(180deg, var(--bean-mid), var(--bean-dark));
  }

  /* back (printed upside down for the fold) */
  .back-content { position: absolute; inset: 0; transform: rotate(180deg); }
  .label--back .bean-strip { height: 40px; }
  .label--back .pink-band { bottom: 40px; height: 12px; }
  .back-copy {
    position: absolute; left: 30px; right: 30px; top: 42px;
    font-family: "Lora", serif; font-size: 14px; line-height: 1.38;
    color: var(--text-light); text-align: center;
  }
  .back-copy p + p { margin-top: 12px; }
  .ingredients {
    position: absolute; left: 52px; right: 52px; top: 272px; height: 128px;
    border: 2px solid var(--brand-pink);
    padding: 18px 20px 0;
    font-family: "Lora", serif; font-size: 14px; line-height: 1.4;
    color: var(--text-light); text-align: center;
  }
  .ingredients-heading { font-weight: 700; letter-spacing: 0.5px; margin-bottom: 4px; }
  .pack-facts {
    position: absolute; left: 90px; right: 90px; top: 420px;
    display: flex; justify-content: space-between;
    font-family: "Lora", serif; font-size: 14px; color: var(--text-light);
  }
</style>
</head>
<body>
<main class="sheet">

  <section class="label label--front">
    <div class="model-photo" role="img" aria-label="Photo of a woman's bare shoulder and back covered in coffee scrub"></div>
    <h1 class="brand-name">BENNY VELVETRIX</h1>
    <div class="product-name">COFFEE SCRUB</div>
    <p class="product-description">Body peeling made of coffee, himalayan salt and additives</p>
    <div class="pink-band"></div>
    <div class="bean-strip" role="img" aria-label="Photo strip of roasted coffee beans"></div>
  </section>
  <div class="caption caption--front">front flip</div>

  <section class="label label--back">
    <div class="back-content">
      <div class="back-copy">
        <p>Hi babe! So you wanna get dirty! Just show me the way to your bath. But first let me give you a proper introduction of myself. My name is Benny and I'm a coffee scrub wearing nothing but 250g of finest arabic coffee and sweet orange flavour and lots of other good stuff.</p>
        <p>By the way I will help you with cellulite, stretch marks, psoriasis, varicose veins, eczema and acne. I'll smooth your lumps and bumps with brown sugar and sea salt, moisturise and tone your skin with cold pressed sweet almond oil, and use vitamins and minerals to work wonders from the outside in. Then I'll make us both smell good with a little orange essence.</p>
      </div>
      <div class="ingredients">
        <div class="ingredients-heading">INGREDIENTS:</div>
        <p>Coffea Robusta Seed Powder (Coffee), Prunus Amygdalus Dulcis (Sweet Almond) Oil, Water (Aqua), Sodium Chloride (Salt), Sucrose (Brown Sugar). All ingredients organic.</p>
      </div>
      <div class="pack-facts">
        <span class="net-weight">NET WT. 200 gms</span>
        <span class="best-before">Best before date:</span>
      </div>
      <div class="pink-band"></div>
      <div class="bean-strip" role="img" aria-label="Photo strip of roasted coffee beans"></div>
    </div>
  </section>
  <div class="caption caption--back">back flip</div>

</main>
</body>
</html>
```